REDESIGN OF WEBSITE HOME PAGE

We are looking for designer to help us create a high end jewelry home page on our new website. The site has to look high end and attractive to high ticket item consumers.

We are upgrading for old site:
www.halvoranteq.com

To New design:
http://dev.pinegatework.com/halvoranteq/index.php/

We're looking to find a designer that can upgrade the home page. Successful engagement will lead to redesigning of this site plus another branded site.

NOTE: This is a public accessed site. All consumers can visit without the need for registering. All retailers will be provided userid/passwords in the back office. Please make the login area discrete.
Updates

Dear everyone, Thank you very much for submmitting. We are reviewing the designs. Please that that the 20% discount is not mean to be the "Center" of the site. It was just a mock up graphic image that we happened to just use as sample.

Project Deadline Extended
Reason: We are going to extend the contest to allow designers to submit changes to our comments.

Dear all designers, Please read and submit your final designs with the followings in mind: Need white backgrounds Take all hot, best, sell products and any other sale pitches off Need the product to sell itself without any special sale pitch We are whole sale mfg = customer need to login to see the actual costs Need a login place not to prominent and not too overwhelming Need social media icons on the bottom Need the top menu bar below the logo - the logo and the model on white background Thanks.

Target Market(s)

Men & Women 30-50 buying high end/ high ticket jewelry & diamonds.

Industry/Entity Type

Jewelry

Colors
3176b5
85acd3
eaf0f6

Requirements
Must have
• Keep current Color Scheme. Logo at the top.
High end look & feel with classical elegant.
We are a manufacturer of high end jewelry. This site is to show case products to end consumers.
Please provide complete Page mock up so we can assess the idea.
Please use the company blue color as central theme.

Please incorporate lady model in the top large banner.
Nice to have
• Magento compliance
Should not have
• Cheap looking design
Too busy of a design
Do not upload designs that are not related to this specific project.
Do not use 20% off message in main banner - Please use Elegant Tag Lines like "Timeless Diamond Jewelry Elegantly Crafted" or anything you can come up with.

```html
<!DOCTYPE html>
<html lang="en">
<head>
<meta charset="utf-8">
<title>Halvoran Teq — Diamond Jewelry</title>
<link rel="stylesheet" href="https://fonts.googleapis.com/css2?family=Open+Sans:wght@300;400;600;700&family=Oswald:wght@300;400&family=Cinzel:wght@400&display=swap">
<style>
:root{
  --header-bg:#fbf9fb;
  --nav:#6cc3e0;
  --accent:#16a6dd;
  --tag-blue:#1b9fd3;
  --ink:#222;
  --muted:#555;
  --search-bg:#2e4d8e;
  --search-dark:#1c2f62;
  --news-bg:#0c1c4b;
  --line:#c9c9c9;
}
*{box-sizing:border-box;margin:0;padding:0}
html,body{width:796px;height:1200px;overflow:hidden;background:#fff}
body{font-family:"Open Sans",Arial,sans-serif;color:var(--ink);position:relative}
a{color:inherit;text-decoration:none}

.site-header{position:absolute;left:0;top:0;width:796px;height:117px;background:var(--header-bg)}
.brand{position:absolute;left:70px;top:28px}
.brand-name{font-size:34px;font-weight:300;letter-spacing:3px;color:#8a8a8a;line-height:1}
.brand-tagline{font-size:11px;color:#8a8a8a;margin-top:8px;letter-spacing:.3px}
.account-links{position:absolute;right:50px;top:9px;font-size:7.5px;color:#222}
.account-links b{font-weight:700}
.live-chat{position:absolute;left:593px;top:42px;width:130px;height:62px}

.main-nav{position:absolute;left:0;top:117px;width:796px;height:34px;background:var(--nav);display:flex;justify-content:center;align-items:center;gap:19px}
.main-nav a{color:#fff;font-size:9.3px;text-transform:uppercase;letter-spacing:.2px}

.hero{position:absolute;left:65px;top:160px;width:666px;height:362px;background:linear-gradient(90deg,#d9d9d9 0%,#9a9a9a 30%,#c8c8c8 55%,#f2f2f2 75%,#fafafa 100%)}
.hero-title{position:absolute;right:18px;top:46px;text-align:right}
.hero-title .line1{font-size:19px;font-weight:300;color:var(--tag-blue)}
.hero-title .line2{font-size:24px;font-weight:400;color:#333;letter-spacing:.5px;margin-top:2px}
.hero-arrow{position:absolute;top:173px;width:33px;height:33px;border-radius:50%;background:#6f6f6f}
.hero-arrow svg{display:block}
.hero-arrow.prev{left:5px}
.hero-arrow.next{right:7px}

.collections{position:absolute;left:65px;top:538px;width:666px;height:127px;display:flex;gap:6px}
.collection-card{position:relative;flex:1;background:#fff;box-shadow:0 6px 6px -4px rgba(0,0,0,.18)}
.collection-card .label{position:absolute;left:8px;top:26px;width:104px;z-index:1;font-family:"Cinzel",serif;color:#8e8e8e;line-height:1.1;white-space:nowrap}
.collection-card .label .small{font-size:16px;display:block}
.collection-card .label .big{font-size:12px;display:block;color:#555}
.collection-card .product{position:absolute;right:8px;top:8px;width:96px;height:110px;border-radius:6px}
.btn-view{position:absolute;left:8px;top:86px;background:var(--accent);color:#fff;font-size:8px;font-weight:600;padding:4px 0;width:56px;text-align:center}

.diamond-search{position:absolute;left:65px;top:689px;width:666px;height:177px;background:var(--search-bg)}
.diamond-search h2{font-size:17px;font-weight:600;color:#fff;text-align:center;padding-top:10px;letter-spacing:.3px}
.diamond-search .rule{position:absolute;left:0;top:38px;width:666px;height:1px;background:rgba(255,255,255,.18)}
.ds-label{position:absolute;top:45px;font-size:8px;color:#fff}
.ds-label b{font-weight:600}
.shape-grid{position:absolute;left:15px;top:66px;width:428px;height:71px;display:flex;border:1px solid #3f5fa3;background:var(--search-dark)}
.shape{flex:1;border-right:1px solid #3f5fa3;display:flex;flex-direction:column;align-items:center;justify-content:flex-end;padding-bottom:6px;font-size:7.5px;color:#fff}
.shape:last-child{border-right:0}
.shape.active{background:#2a4a9c}
.shape svg{margin-bottom:9px}
.price-box{position:absolute;left:452px;top:66px;width:199px;height:71px;background:var(--search-dark)}
.btn-search{position:absolute;left:268px;top:143px;width:75px;height:25px;background:var(--accent);color:#fff;font-size:9px;display:flex;align-items:center;justify-content:center}
.link-advanced{position:absolute;left:358px;top:150px;font-size:8.5px;color:#fff;text-decoration:underline}

.newsletter{position:absolute;left:0;top:881px;width:796px;height:112px;background:var(--news-bg);text-align:center;color:#fff}
.newsletter h2{font-size:18px;font-weight:300;margin-top:12px}
.newsletter p{font-size:8px;margin-top:10px}
.news-form{position:absolute;left:167px;top:64px;display:flex}
.news-input{width:405px;height:30px;background:#f0f0f0;color:#9a9a9a;font-size:7.5px;text-align:left;padding:10px 11px}
.news-submit{width:67px;height:30px;background:var(--accent);font-size:8.5px;font-weight:600;display:flex;align-items:center;justify-content:center}

.site-footer{position:absolute;left:0;top:1012px;width:796px}
.footer-col{position:absolute;top:0}
.footer-col h3{font-family:"Oswald",sans-serif;font-weight:300;font-size:14px;color:#333;margin-bottom:10px}
.footer-col li{list-style:none;font-size:8.3px;color:#333;line-height:21px}
.social{display:flex;gap:7px;margin-top:14px}
.social span{width:28px;height:28px;border-radius:50%;border:2px solid #9bb0c8}
.social .s1{background:#3b5a9a}.social .s2{background:#2aa6df}.social .s3{background:#f26522}
.footer-rule{position:absolute;left:59px;top:1164px;width:680px;height:1px;background:var(--line)}
.copyright{position:absolute;left:0;top:1177px;width:796px;text-align:center;font-size:7.5px;color:#888}
</style>
</head>
<body>

<header class="site-header">
  <div class="brand">
    <div class="brand-name">HALVORAN TEQ</div>
    <div class="brand-tagline">The Diamond Company with a Difference</div>
  </div>
  <div class="account-links">Welcome visitor you can <b>Login</b> or <b>Create An Account</b></div>
  <svg class="live-chat" viewBox="0 0 130 62" aria-label="Live chat">
    <rect x="0" y="10" width="122" height="46" rx="6" fill="#1e72b8"/>
    <rect x="44" y="0" width="50" height="24" rx="5" fill="#8fc640"/>
    <text x="69" y="17" text-anchor="middle" font-family="Open Sans, sans-serif" font-size="14" font-weight="700" fill="#fff">LIVE</text>
    <text x="80" y="46" text-anchor="middle" font-family="Open Sans, sans-serif" font-size="17" font-weight="700" fill="#fff">CHAT</text>
    <circle cx="22" cy="33" r="7" fill="#fff"/>
    <rect x="12" y="41" width="20" height="10" rx="5" fill="#fff"/>
  </svg>
</header>

<nav class="main-nav">
  <a href="#">Home</a><a href="#">Diamonds</a><a href="#">Rings</a><a href="#">Earrings</a><a href="#">Necklaces</a><a href="#">Bracelets</a><a href="#">Pendant</a><a href="#">Encyclopedia</a><a href="#">Store Locator</a><a href="#">Contact Us</a>
</nav>

<section class="hero" role="img" aria-label="Black and white photograph of a woman model wearing diamond drop earrings and a diamond ring">
  <div class="hero-title">
    <div class="line1">Timeless Diamond Jewelry</div>
    <div class="line2">ELEGANTLY CRAFTED</div>
  </div>
  <div class="hero-arrow prev"><svg width="33" height="33" viewBox="0 0 33 33"><path d="M19 10l-6 6.5 6 6.5" stroke="#fff" stroke-width="2.5" fill="none"/></svg></div>
  <div class="hero-arrow next"><svg width="33" height="33" viewBox="0 0 33 33"><path d="M14 10l6 6.5-6 6.5" stroke="#fff" stroke-width="2.5" fill="none"/></svg></div>
</section>

<section class="collections">
  <div class="collection-card">
    <div class="label"><span class="small">Jewelry</span><span class="big">COLLECTIONS</span></div>
    <div class="product" role="img" aria-label="Photo of diamond cluster drop earrings" style="background:linear-gradient(135deg,#f4f4f4,#d6d6d6)"></div>
    <a class="btn-view" href="#">VIEW ALL</a>
  </div>
  <div class="collection-card">
    <div class="label"><span class="small">JEWELRY</span><span class="big">COLLECTIONS</span></div>
    <div class="product" role="img" aria-label="Photo of a gold ring set with diamonds" style="background:linear-gradient(135deg,#faf3e0,#e2c77a)"></div>
    <a class="btn-view" href="#">VIEW ALL</a>
  </div>
  <div class="collection-card">
    <div class="label"><span class="small">DIAMOND</span><span class="big">COLLECTIONS</span></div>
    <div class="product" role="img" aria-label="Photo of a diamond flower pendant on a chain" style="background:linear-gradient(135deg,#f6f6f6,#d2d2d2)"></div>
    <a class="btn-view" href="#">VIEW ALL</a>
  </div>
</section>

<section class="diamond-search">
  <h2>DIAMOND SEARCH</h2>
  <div class="rule"></div>
  <div class="ds-label" style="left:16px"><b>SELECT SHAPE</b> - just click on the shape which you want to buy</div>
  <div class="ds-label" style="left:440px"><b>PRICE RANGE</b> - just slide the slider to set the price range</div>
  <div class="shape-grid">
    <div class="shape active"><svg width="30" height="30"><circle cx="15" cy="15" r="14" fill="#e8e8e8"/></svg>Round</div>
    <div class="shape"><svg width="20" height="38"><ellipse cx="10" cy="19" rx="7" ry="18" fill="#e8e8e8"/></svg>Marquise</div>
    <div class="shape"><svg width="30" height="28"><rect x="2" y="2" width="26" height="24" rx="6" fill="#e8e8e8"/></svg>Radiant</div>
    <div class="shape"><svg width="24" height="34"><path d="M12 1C5 12 2 20 2 24a10 10 0 0020 0c0-4-3-12-10-23z" fill="#e8e8e8"/></svg>Pear</div>
    <div class="shape"><svg width="32" height="22"><rect x="1" y="1" width="30" height="20" fill="#e8e8e8"/></svg>Emerald</div>
    <div class="shape"><svg width="30" height="28"><path d="M2 2h26L15 27z" fill="#e8e8e8"/></svg>Trillions</div>
    <div class="shape"><svg width="30" height="30"><path d="M15 1l14 14-14 14L1 15z" fill="#e8e8e8"/></svg>Princes</div>
    <div class="shape"><svg width="30" height="28"><path d="M15 27L3 14A7 7 0 0115 5a7 7 0 0112 9z" fill="#e8e8e8"/></svg>Heart</div>
    <div class="shape"><svg width="24" height="32"><ellipse cx="12" cy="16" rx="11" ry="15" fill="#e8e8e8"/></svg>Oval</div>
  </div>
  <div class="price-box">
    <svg width="199" height="71" viewBox="0 0 199 71" font-family="Open Sans, sans-serif">
      <rect x="14" y="7" width="30" height="12" rx="2" fill="#2d6fb5"/>
      <text x="29" y="16" text-anchor="middle" font-size="7.5" fill="#fff">$1000</text>
      <rect x="150" y="7" width="34" height="12" rx="2" fill="#2d6fb5"/>
      <text x="167" y="16" text-anchor="middle" font-size="7.5" fill="#fff">$25000</text>
      <rect x="8" y="32" width="183" height="6" rx="3" fill="#c9c9c9"/>
      <rect x="29" y="32" width="137" height="6" fill="#1f8fd6"/>
      <circle cx="29" cy="35" r="5" fill="#ddd" stroke="#999"/>
      <circle cx="166" cy="35" r="5" fill="#ddd" stroke="#999"/>
      <g fill="#fff" font-size="5.5" text-anchor="middle">
        <text x="11" y="55">0</text><text x="28" y="55">1000</text><text x="44" y="55">2000</text><text x="61" y="55">5000</text><text x="79" y="55">8000</text><text x="100" y="55">10000</text><text x="125" y="55">15000</text><text x="151" y="55">20000</text><text x="181" y="55">30000</text>
      </g>
    </svg>
  </div>
  <a class="btn-search" href="#">SEARCH</a>
  <a class="link-advanced" href="#">Advanced Search</a>
</section>

<section class="newsletter">
  <h2>Subscribe Our Newsletter</h2>
  <p>To get weekly, monthly update, special news, speical offer &amp; gift please subscribe our newsletter.</p>
  <div class="news-form">
    <div class="news-input">TYPE YOUR EMAIL ID HERE</div>
    <div class="news-submit">SUBMIT</div>
  </div>
</section>

<footer class="site-footer">
  <div class="footer-col" style="left:65px"><h3>Information</h3><ul><li>- Site Map</li><li>- Search Terms</li><li>- Advanced Search</li><li>- Orders and Returns</li><li>- Contact Us</li></ul></div>
  <div class="footer-col" style="left:203px"><h3>Why Buy From Us</h3><ul><li>- Shipping &amp; Returns</li><li>- Secure Shopping</li><li>- International Shipping</li><li>- Affiliates</li><li>- Group Sales</li></ul></div>
  <div class="footer-col" style="left:356px"><h3>My Account</h3><ul><li>- Sign In</li><li>- View Cart</li><li>- My Wishlist</li><li>- Track My Order</li><li>- Help</li></ul></div>
  <div class="footer-col" style="left:470px"><h3>Store Location</h3><ul><li>Halvoran Teq Corp.</li><li>214 Larkmoor Ave # 6</li><li>Brenfield, NY 10482</li><li>Tel: +(555) 318-2094</li><li>Email: info@halvoranteq.com</li></ul></div>
  <div class="footer-col" style="left:624px"><h3>Get In Touch With Us</h3><div class="social" aria-label="Social media links"><span class="s1"></span><span class="s2"></span><span class="s3"></span></div></div>
</footer>
<div class="footer-rule"></div>
<div class="copyright">© 2014, All Rights Reserved, HalvoranTeq</div>

</body>
</html>
```